Direct to Consumer extended service contract business with a new disruptive business model needs a

We need a customized wordpress design for a company called 'Bright Harbor Assurance'.
We provide an innovative and unique service contract protection program direct to consumers. This program provides monthly coverage for all electronics purchased in the last 4 years and all electronics the consumer purchases in the future for a low monthly fee. The overall design should communicate a sense of legitimacy, ethics, and superior customer service and support (in an industry that has a huge PR issue to overcome).
Electronics is the first product group, other product groups with different price points to launch in the future..

Target Market(s)

All purchasers of electronic goods...all demographics

Industry/Entity Type

Electronics

Font styles to use
Sans Serif

Requirements
Must have
• Customer Testimonials
Industry News
Customer ratings
Blog posts
Call to action messaging
Like the functional elements and design of quillmesa.example (need to be better)
Nice to have
• Like to see video testimonials
Social network "whats trending related to electronics or service contract industry"
Easy way to register products for warranty

```html
<!DOCTYPE html>
<html lang="en">
<head>
<meta charset="utf-8">
<title>Bright Harbor Assurance</title>
<link href="https://fonts.googleapis.com/css2?family=PT+Sans:ital,wght@0,400;0,700;1,400&family=Roboto+Condensed:ital,wght@0,700;1,700&display=swap" rel="stylesheet">
<style>
:root{
  --green:#0f7a3a;
  --green-bright:#1a9a2a;
  --green-dark:#0b5e2c;
  --red:#d61d1d;
  --dark:#232323;
  --ink:#1a1a1a;
  --grey:#8a8a8a;
  --white:#ffffff;
  --star-red:#e02a1f;
  --star-blue:#2a7be0;
  --star-green:#7cc21e;
}
*{box-sizing:border-box;margin:0;padding:0}
html,body{width:1200px;height:2748px;overflow:hidden}
body{position:relative;background:var(--white);font-family:"PT Sans",Arial,sans-serif;color:var(--ink)}
.abs{position:absolute}

/* top bar */
.topbar{left:0;top:0;width:1200px;height:27px;background:linear-gradient(var(--green-bright),#138a22);display:flex;justify-content:flex-end;align-items:center;gap:22px;padding-right:22px;color:var(--white);font-weight:700;font-size:15px}

/* header */
.header{left:0;top:27px;width:1200px;height:92px;background:var(--white)}
.brand{left:88px;top:30px;display:flex;align-items:center;gap:12px}
.brand-mark{width:34px;height:34px;background:var(--green)}
.brand-name{font-family:"PT Sans",sans-serif;font-weight:700;font-size:24px;line-height:26px;color:var(--green);text-transform:uppercase;width:230px}
.nav{right:32px;top:36px;display:flex;gap:26px;font-size:19px;letter-spacing:.5px;color:#333}
.nav a{color:inherit;text-decoration:none;padding-bottom:5px}
.nav a.active{color:var(--green);border-bottom:3px solid var(--green)}

/* hero */
.hero{left:0;top:119px;width:1200px;height:531px;background:repeating-linear-gradient(45deg,#262626 0 3px,#1e1e1e 3px 6px)}
.hero-visual{left:55px;top:55px;width:559px;height:343px;background:linear-gradient(#e9e9e9,#c9c9c9);border:14px solid #111;border-bottom-width:26px;border-radius:10px}
.hero-lines{right:92px;top:115px;display:flex;flex-direction:column;align-items:flex-end;gap:9px}
.hero-lines span{background:#000;color:var(--white);font-weight:700;font-size:38px;line-height:41px;padding:0 6px;letter-spacing:1.5px}
.cta{left:663px;top:282px;width:445px;height:57px;background:linear-gradient(#ee2a1a,#c41010);color:var(--white);font-size:38px;font-weight:700;display:flex;align-items:center;justify-content:center;letter-spacing:.5px}

/* features */
.features{left:101px;top:568px;width:998px;height:165px;background:var(--white);display:flex;gap:9px;padding:18px 14px}
.feature{width:317px}
.feature-head{height:70px;background:var(--red);color:var(--white);display:flex;align-items:center;gap:14px;padding-left:16px;font-family:"PT Sans",sans-serif;font-weight:700;font-size:23px;line-height:23px;text-transform:uppercase}
.feature-head svg{flex:none}
.feature ul{list-style:none;margin-top:8px;font-size:15px;line-height:20px;color:#222}

/* green bands */
.band{left:0;width:1200px;background:repeating-linear-gradient(0deg,#137b3a 0 2px,#0f7535 2px 4px)}
.section-title{width:100%;text-align:center;font-family:"Roboto Condensed",sans-serif;font-style:italic;font-weight:700;font-size:31px}
.band .section-title{color:var(--white)}
.white .section-title{color:var(--red)}

.arrow{width:0;height:0;border-top:17px solid transparent;border-bottom:17px solid transparent}
.arrow.left{border-right:17px solid var(--white)}
.arrow.right{border-left:17px solid var(--white)}

/* ratings */
.ratings{top:771px;height:284px}
.rating{display:flex;gap:14px;align-items:flex-start;color:var(--white)}
.rating-dot{width:100px;height:100px;border-radius:50%;flex:none}
.rating h3{font-size:28px;font-weight:400;line-height:30px}
.rating p{font-size:20px;line-height:24px;width:200px}
.stars{display:flex;gap:6px;margin-top:6px}

/* cards */
.card{width:317px}
.card-photo{width:317px;height:236px}
.card h4{font-size:24px;font-weight:400;margin-top:8px;line-height:26px;color:var(--ink)}
.card .meta{font-size:13px;font-style:italic;font-weight:700;color:var(--red)}
.card hr{border:0;border-top:2px solid #ccc;margin:10px 0 8px}
.card .excerpt{font-size:14px;font-style:italic;color:var(--grey);line-height:20px}
.blog .meta{font-weight:400}

/* testimonials */
.testimonials{top:1612px;height:350px}
.video{width:337px;height:185px;border:2px solid #9cc4a8;background:linear-gradient(90deg,#0d2e5c,#1c4f8a 60%,#133a6c);display:flex;align-items:center;justify-content:center}

/* footer */
.footer{left:0;top:2468px;width:1200px;height:245px;background:var(--green);color:var(--white)}
.footer h5{font-family:"Roboto Condensed",sans-serif;font-size:19px;font-weight:700;text-transform:uppercase;padding-bottom:5px;border-bottom:2px solid var(--white)}
.footer-links{display:grid;grid-template-columns:130px 100px;row-gap:3px;font-size:16px;font-weight:700;margin-top:20px}
.social-icons{display:flex;gap:6px}
.social-icons span{width:36px;height:36px;background:#3b5b9a;border-radius:4px}
.feed{left:425px;top:78px;width:308px;height:154px;background:var(--white);padding:14px 16px;display:flex;flex-direction:column;gap:10px}
.feed-item{display:flex;gap:12px;align-items:center}
.feed-item i{width:36px;height:36px;border-radius:50%;background:var(--red);flex:none}
.feed-item b{display:block;color:var(--red);font-size:10px;text-transform:uppercase}
.feed-item small{display:block;color:#222;font-size:10px}
.contact-list{list-style:none;margin-top:18px;font-size:15px;font-style:italic;font-weight:700;line-height:21px}
.contact-list li{display:flex;align-items:center;gap:10px}
.contact-list li span.pad{width:14px}
.copyright{left:0;top:2713px;width:1200px;height:35px;background:#111;color:var(--white);font-size:14px;font-weight:700;display:flex;align-items:center;justify-content:center}
</style>
</head>
<body>

<div class="abs topbar"><span>Login</span><span>Support</span><span>Call: 555-014-0199</span></div>

<header class="abs header">
  <div class="abs brand" style="top:8px">
    <span class="brand-mark"></span>
    <span class="brand-name">Bright Harbor Assurance</span>
  </div>
  <nav class="abs nav">
    <a class="active">HOME</a><a>PLANS</a><a>BENEFITS</a><a>ABOUT US</a><a>BLOG</a><a>NEWS</a><a>CONTACT</a>
  </nav>
</header>

<section class="abs hero">
  <div class="abs hero-visual" role="img" aria-label="Laptop showing the quote form and store ratings of the site"></div>
  <div class="abs hero-lines">
    <span>BUYS YOUR DEVICE</span>
    <span>PAY MONTHLY TO SECURE</span>
    <span>CLAIM/FIX YOUR DEVICE</span>
  </div>
  <div class="abs cta">GET FREE QUOTE</div>
</section>

<section class="abs features">
  <div class="feature">
    <div class="feature-head">
      <svg width="44" height="36" viewBox="0 0 44 36"><rect x="3" y="9" width="38" height="20" rx="10" fill="#fff"/><rect x="10" y="17" width="10" height="3" fill="#d61d1d"/><rect x="13.5" y="13.5" width="3" height="10" fill="#d61d1d"/><circle cx="30" cy="16" r="2.2" fill="#d61d1d"/><circle cx="34" cy="21" r="2.2" fill="#d61d1d"/></svg>
      <span>Purchase in low<br>rates</span>
    </div>
    <ul><li>- 1000 products available online</li><li>- Low as price as compare to market price</li><li>- Easy to purchase any product</li></ul>
  </div>
  <div class="feature">
    <div class="feature-head">
      <svg width="40" height="44" viewBox="0 0 40 44"><path d="M20 2 L38 8 V22 C38 33 29 40 20 43 C11 40 2 33 2 22 V8 Z" fill="#fff"/></svg>
      <span>Protect devices<br>by paying monthy</span>
    </div>
    <ul><li>- Pay montly fee</li><li>- Low rates as compate to others</li><li>- Secure your device in advance</li></ul>
  </div>
  <div class="feature">
    <div class="feature-head">
      <svg width="42" height="36" viewBox="0 0 42 36" fill="none" stroke="#fff" stroke-width="4"><path d="M6 16 V8 H34"/><path d="M36 20 V28 H8"/><path d="M28 2 L35 8 L28 14" /><path d="M14 22 L7 28 L14 34"/></svg>
      <span>Claim and fix<br>your device</span>
    </div>
    <ul><li>- Claim your money you have paid</li><li>- Fix your broken devices</li><li>- Fast and reliable</li></ul>
  </div>
</section>

<section class="abs band ratings">
  <h2 class="abs section-title" style="top:28px">Customer Raiting</h2>
  <div class="abs arrow left" style="left:24px;top:154px"></div>
  <div class="abs arrow right" style="left:1107px;top:154px"></div>
  <div class="abs rating" style="left:70px;top:118px">
    <span class="rating-dot" style="background:#2a2a2a"></span>
    <div><h3>Orchard Store</h3><p>some info came here with description.</p>
      <svg class="stars" width="170" height="26" viewBox="0 0 170 26"><g fill="var(--star-red)"><polygon id="st" points="13,1 16.5,9 25,9.5 18.5,15 20.5,24 13,19 5.5,24 7.5,15 1,9.5 9.5,9"/><use href="#st" x="34"/><use href="#st" x="68"/><use href="#st" x="102"/><use href="#st" x="136"/></g></svg>
    </div>
  </div>
  <div class="abs rating" style="left:420px;top:118px">
    <span class="rating-dot" style="background:#1c1c1c;border:3px dashed #fff"></span>
    <div><h3>Riverbend Store</h3><p>some info came here with description.</p>
      <svg class="stars" width="170" height="26" viewBox="0 0 170 26"><g fill="var(--star-blue)"><use href="#st"/><use href="#st" x="34"/><use href="#st" x="68"/><use href="#st" x="102"/><use href="#st" x="136"/></g></svg>
    </div>
  </div>
  <div class="abs rating" style="left:783px;top:116px">
    <span class="rating-dot" style="background:#e3322a"></span>
    <div><h3>Plusline Store</h3><p>some info came here with description.</p>
      <svg class="stars" width="170" height="26" viewBox="0 0 170 26"><g fill="var(--star-green)"><use href="#st"/><use href="#st" x="34"/><use href="#st" x="68"/><use href="#st" x="102"/><use href="#st" x="136"/></g></svg>
    </div>
  </div>
</section>

<section class="abs white news" style="left:0;top:1055px;width:1200px;height:557px">
  <h2 class="abs section-title" style="top:38px">Industry News</h2>
  <article class="abs card" style="left:115px;top:101px">
    <div class="card-photo" role="img" aria-label="Smiling shopper using a laptop in an electronics store" style="background:linear-gradient(135deg,#3d5a80,#b9c4d4)"></div>
    <h4>Lorem ipsum nipsum saye</h4><p class="meta">Posted on: Sep 29th, 2014</p><hr>
    <p class="excerpt">Lorem ipsum nipsum saye Lorem ipsum nipsum saye. Lorem ipsum nipsum saye Lorem ipsum nipsum saye.</p>
  </article>
  <article class="abs card" style="left:441px;top:101px">
    <div class="card-photo" role="img" aria-label="Woman touching a digital interface screen" style="background:linear-gradient(135deg,#dfe6ee,#9fb6cc)"></div>
    <h4>Lorem ipsum nipsum saye</h4><p class="meta">Posted on: Sep 29th, 2014</p><hr>
    <p class="excerpt">Lorem ipsum nipsum saye Lorem ipsum nipsum saye. Lorem ipsum nipsum saye Lorem ipsum nipsum saye.</p>
  </article>
  <article class="abs card" style="left:768px;top:101px">
    <div class="card-photo" role="img" aria-label="Couple looking at televisions in a store" style="background:linear-gradient(135deg,#2e6aa0,#b8c7d4)"></div>
    <h4>Lorem ipsum nipsum saye</h4><p class="meta">Posted on: Sep 29th, 2014</p><hr>
    <p class="excerpt">Lorem ipsum nipsum saye Lorem ipsum nipsum saye. Lorem ipsum nipsum saye Lorem ipsum nipsum saye.</p>
  </article>
</section>

<section class="abs band testimonials">
  <h2 class="abs section-title" style="top:38px">Customer Testimonials</h2>
  <div class="abs arrow left" style="left:47px;top:144px"></div>
  <div class="abs arrow right" style="left:1130px;top:144px"></div>
  <div class="abs video" style="left:88px;top:108px" role="img" aria-label="Video testimonial from a customer"><svg width="56" height="56" viewBox="0 0 56 56"><circle cx="28" cy="28" r="27" fill="#6cbd2a"/><polygon points="22,15 42,28 22,41" fill="#fff"/></svg></div>
  <div class="abs video" style="left:431px;top:108px" role="img" aria-label="Video testimonial from a customer"><svg width="56" height="56" viewBox="0 0 56 56"><circle cx="28" cy="28" r="27" fill="#6cbd2a"/><polygon points="22,15 42,28 22,41" fill="#fff"/></svg></div>
  <div class="abs video" style="left:773px;top:108px" role="img" aria-label="Video testimonial from a customer"><svg width="56" height="56" viewBox="0 0 56 56"><circle cx="28" cy="28" r="27" fill="#6cbd2a"/><polygon points="22,15 42,28 22,41" fill="#fff"/></svg></div>
</section>

<section class="abs white blog" style="left:0;top:1962px;width:1200px;height:506px">
  <h2 class="abs section-title" style="top:52px">Welcome to our Blog</h2>
  <article class="abs card" style="left:115px;top:125px">
    <div class="card-photo" role="img" aria-label="Technician repairing electronics at a workbench" style="background:linear-gradient(135deg,#1f3f7a,#8f9aa8)"></div>
    <h4>Lorem ipsum nipsum saye</h4><p class="meta">Sep 29th, 2014 / 10 Comments</p>
  </article>
  <article class="abs card" style="left:441px;top:125px">
    <div class="card-photo" role="img" aria-label="Hands typing on a laptop keyboard" style="background:linear-gradient(135deg,#e4e6e8,#b7bcc2)"></div>
    <h4>Lorem ipsum nipsum saye</h4><p class="meta">Sep 29th, 2014 / 10 Comments</p>
  </article>
  <article class="abs card" style="left:768px;top:125px">
    <div class="card-photo" role="img" aria-label="Woman holding two electronic devices" style="background:linear-gradient(135deg,#bcd8ee,#e7c7ad)"></div>
    <h4>Lorem ipsum nipsum saye</h4><p class="meta">Sep 29th, 2014 / 10 Comments</p>
  </article>
</section>

<footer class="abs footer">
  <div class="abs" style="left:97px;top:38px;width:229px">
    <h5>Welcome to BHA</h5>
    <div class="footer-links"><span>Our Plans</span><span>Blog</span><span>Benefits</span><span>News</span><span>About us</span><span>Support</span><span>Contact us</span><span>Terms</span></div>
  </div>
  <div class="abs" style="left:425px;top:28px;width:308px;display:flex;align-items:center;gap:12px">
    <h5 style="border:0">Social Media Feed</h5>
    <div class="social-icons"><span></span><span style="background:#2fa6d8"></span><span style="background:#c4302b"></span></div>
  </div>
  <div class="abs feed">
    <div class="feed-item"><i></i><div><b>Name of person</b><small>This is an example of tweet or social feed.</small></div></div>
    <div class="feed-item"><i></i><div><b>Name of person</b><small>This is an example of tweet or social feed.</small></div></div>
    <div class="feed-item"><i></i><div><b>Name of person</b><small>This is an example of tweet or social feed.</small></div></div>
  </div>
  <div class="abs" style="left:824px;top:38px;width:233px">
    <h5>Contact us</h5>
    <ul class="contact-list">
      <li><svg width="14" height="14" viewBox="0 0 14 14"><circle cx="7" cy="7" r="6" fill="#fff"/><path d="M7 1 V13 M1 7 H13" stroke="#0f7a3a"/></svg>4410 Meadow Lane</li>
      <li><span class="pad"></span>NY 10099 America</li>
      <li><svg width="14" height="14" viewBox="0 0 14 14"><rect x="3" y="1" width="8" height="12" rx="1" fill="#fff"/></svg>Ph: (001) 555-0199</li>
      <li><svg width="14" height="14" viewBox="0 0 14 14"><rect x="1" y="3" width="12" height="9" fill="#fff"/><path d="M1 3 L7 8 L13 3" stroke="#0f7a3a" fill="none"/></svg>Email: hello@brightharbor.example</li>
    </ul>
  </div>
</footer>

<div class="abs copyright">Copyright © 2014 Bright Harbor Assurance</div>

</body>
</html>
```